Classy, Elegant, Simple Business Card Design

Looking to have a classy, simple, and elegant design. Want a top notch designed business card. I really like the look of the new torvane credit card. I also like the design I attached. I am trying to reach 21-29 year old females for booking us for there wedding or event. We offer Disc Jockey Service, Photo Booth Rentals, and Uplighting .

Target Market(s)

21-28 year old females

Contact Information for Business Card

Has to have logo, website, email, and phone number

Font styles to use
Other font styles liked:
• open to font choice, modern, clean
Designer to choose
33a6d7
0791cd
0555a3
ffffff

Requirements
Must have
• Has to have logo, website, email, and phone number
Nice to have
• I really like the design of the new torvane credit card. I also included my logo and some designs I like
Should not have
• clutter or too much info

```html
<!DOCTYPE html>
<html lang="en">
<head>
<meta charset="utf-8">
<title>Tidecrest Events – Business Card</title>
<link rel="stylesheet" href="https://fonts.googleapis.com/css2?family=Nunito+Sans:wght@400;600;700&family=Roboto:wght@400&display=swap">
<style>
  :root {
    --backdrop: #e8e3dd;
    --card-light: #ffffff;
    --card-frost: #eef1f4;
    --brand-deep: #0555a3;
    --brand-mid: #0791cd;
    --brand-sky: #33a6d7;
    --wave-silver: #a7abb0;
    --ink-light: #f2eee6;
    --ink-soft: #dfe6ee;
  }
  * { margin: 0; padding: 0; box-sizing: border-box; }
  html, body {
    width: 1200px; height: 1054px; overflow: hidden;
    background: var(--backdrop);
  }
  .business-card {
    position: absolute; left: 100px; top: 226px;
    width: 1000px; height: 602px;
    background: linear-gradient(160deg, var(--card-light), var(--card-frost));
    box-shadow: 0 10px 30px rgba(0,0,0,0.15);
    overflow: hidden;
  }
  .card-wave { position: absolute; inset: 0; width: 1000px; height: 602px; }
  .brand-lockup {
    position: absolute; left: 91px; top: 110px;
    display: flex; flex-direction: column; align-items: flex-start; gap: 28px;
  }
  .brand-dot {
    width: 96px; height: 96px; border-radius: 50%;
    background: var(--brand-mid);
  }
  .brand-name {
    font-family: "Nunito Sans", sans-serif; font-weight: 600;
    font-size: 46px; letter-spacing: 2px; color: var(--brand-deep);
  }
  .contact-block {
    position: absolute; right: 54px; top: 300px;
    text-align: right; color: var(--ink-light);
  }
  .person-name {
    font-family: "Nunito Sans", sans-serif; font-weight: 700;
    font-size: 40px; line-height: 1.1;
  }
  .person-role {
    font-family: "Roboto", sans-serif; font-size: 23px;
    margin-top: 6px; color: var(--ink-soft);
  }
  .contact-list { list-style: none; margin-top: 52px; }
  .contact-item {
    font-family: "Roboto", sans-serif; font-size: 23px;
    display: flex; justify-content: flex-end; align-items: center; gap: 6px;
    height: 38px;
  }
  .contact-icon { width: 22px; height: 22px; fill: var(--ink-light); }
</style>
</head>
<body>
  <section class="business-card">
    <svg class="card-wave" viewBox="0 0 1000 602" aria-hidden="true">
      <defs>
        <linearGradient id="waveBlue" x1="0" y1="1" x2="1" y2="0">
          <stop offset="0" stop-color="#0a4f8f"/>
          <stop offset="0.6" stop-color="#1a6aa8"/>
          <stop offset="1" stop-color="#0791cd"/>
        </linearGradient>
      </defs>
      <path d="M0,508 C300,446 700,300 982,0 L1000,0 L1000,602 L0,602 Z" fill="var(--wave-silver)"/>
      <path d="M0,540 C300,472 710,330 1000,25 L1000,602 L0,602 Z" fill="url(#waveBlue)"/>
    </svg>

    <div class="brand-lockup">
      <div class="brand-dot"></div>
      <div class="brand-name">TIDECREST EVENTS</div>
    </div>

    <div class="contact-block">
      <h1 class="person-name">Owen Hartley</h1>
      <p class="person-role">Founder &amp; CEO</p>
      <ul class="contact-list">
        <li class="contact-item">555 0142 0187
          <svg class="contact-icon" viewBox="0 0 24 24"><path d="M6.6 10.8a15 15 0 0 0 6.6 6.6l2.2-2.2c.3-.3.7-.4 1-.2 1.1.4 2.3.6 3.6.6.6 0 1 .4 1 1V20c0 .6-.4 1-1 1A17 17 0 0 1 3 4c0-.6.4-1 1-1h3.5c.6 0 1 .4 1 1 0 1.3.2 2.5.6 3.6.1.3 0 .7-.2 1z"/></svg>
        </li>
        <li class="contact-item">owen@tidecrest.com
          <svg class="contact-icon" viewBox="0 0 24 24"><path d="M3 5h18v14H3z M4 6.5v.3l8 5.4 8-5.4v-.3z" fill-rule="evenodd"/></svg>
        </li>
        <li class="contact-item">www.tidecrest.com
          <svg class="contact-icon" viewBox="0 0 24 24"><path d="M12 2a10 10 0 1 0 0 20 10 10 0 0 0 0-20zm6.9 6h-3a15 15 0 0 0-1.4-3.9A8 8 0 0 1 18.9 8zM12 4c.8 1.2 1.5 2.5 1.9 4h-3.8c.4-1.5 1.1-2.8 1.9-4zM4.3 14a8 8 0 0 1 0-4h3.4a16 16 0 0 0 0 4zm.8 2h3a15 15 0 0 0 1.4 3.9A8 8 0 0 1 5.1 16zm3-8h-3a8 8 0 0 1 4.4-3.9C8.8 5.3 8.4 6.6 8.1 8zM12 20c-.8-1.2-1.5-2.5-1.9-4h3.8c-.4 1.5-1.1 2.8-1.9 4zm2.3-6H9.7a14 14 0 0 1 0-4h4.6a14 14 0 0 1 0 4zm.2 5.9c.6-1.2 1.1-2.5 1.4-3.9h3a8 8 0 0 1-4.4 3.9zM16.3 14a16 16 0 0 0 0-4h3.4a8 8 0 0 1 0 4z"/></svg>
        </li>
      </ul>
    </div>
  </section>
</body>
</html>
```